Water ATM Card

Need a design for water ATM cards. Size of card is 3.375 x 2.125 inch
On the Front include the Cedar hollow Logo.
Bottom right corner should have Price $100
On the Back
This card is to be used to access water refills at any Cedar Hollow Water Vending Machines.
Please contact (869) 418 2930 or (869) 534 1276 or email clearflowbox@mailvista.example for any assistance or recharging of card.

```html
<!DOCTYPE html>
<html lang="en">
<head>
<meta charset="utf-8">
<title>Cedar Hollow Water Card</title>
<link href="https://fonts.googleapis.com/css2?family=Poppins:ital,wght@0,400;0,500;0,600;0,700;1,600&display=swap" rel="stylesheet">
<style>
  :root {
    --backdrop: #a3a3a3;
    --card-white: #ffffff;
    --card-mist: #e3f0fb;
    --brand-blue: #1f6cb8;
    --navy-blue: #1e4d9e;
    --fresh-green: #2f9a3c;
    --ink: #222222;
    --water-deep: #2f78b8;
    --water-mid: #6fb0e0;
    --water-light: #cfe6f7;
  }
  * { margin: 0; padding: 0; box-sizing: border-box; }
  html, body { width: 1093px; height: 1200px; overflow: hidden; }
  body {
    background: var(--backdrop);
    font-family: "Poppins", sans-serif;
    position: relative;
  }
  .card {
    position: absolute;
    width: 580px;
    height: 356px;
    border-radius: 26px;
    overflow: hidden;
    background: linear-gradient(160deg, var(--card-mist) 0%, var(--card-white) 55%, var(--card-white) 100%);
  }
  .card--front { left: 264px; top: 226px; }
  .card--back { left: 264px; top: 621px; }

  .water-photo {
    position: absolute;
    left: 0;
    width: 100%;
  }
  .card--front .water-photo {
    top: 150px;
    height: 170px;
    background: linear-gradient(180deg, rgba(207,230,247,0) 0%, var(--water-mid) 22%, var(--water-deep) 48%, var(--water-mid) 72%, rgba(207,230,247,0) 100%);
    clip-path: polygon(0 15%, 30% 12%, 60% 30%, 85% 40%, 100% 20%, 100% 95%, 80% 85%, 50% 80%, 0 65%);
  }
  .card--back .water-photo {
    bottom: 0;
    height: 90px;
    background: linear-gradient(180deg, rgba(207,230,247,0) 0%, var(--water-mid) 45%, var(--water-deep) 100%);
    clip-path: polygon(0 30%, 30% 40%, 55% 75%, 70% 100%, 0 100%);
  }

  .brand {
    position: absolute;
    text-align: center;
    color: var(--brand-blue);
  }
  .brand__name {
    display: flex;
    align-items: center;
    justify-content: center;
    gap: 8px;
    font-weight: 600;
    letter-spacing: 0.5px;
    white-space: nowrap;
  }
  .brand__dot {
    display: inline-block;
    border-radius: 50%;
    background: var(--fresh-green);
  }
  .brand__tagline {
    font-weight: 400;
    letter-spacing: 0.6px;
    white-space: nowrap;
  }
  .card--front .brand { left: 0; right: 0; top: 82px; }
  .card--front .brand__name { font-size: 27px; line-height: 1.1; }
  .card--front .brand__dot { width: 16px; height: 16px; }
  .card--front .brand__tagline { font-size: 17px; line-height: 1.2; }

  .price {
    position: absolute;
    right: 55px;
    top: 302px;
    font-size: 22px;
    font-weight: 600;
    color: var(--fresh-green);
  }

  .usage-note {
    position: absolute;
    left: 30px;
    top: 54px;
    font-size: 16px;
    line-height: 24px;
    font-weight: 700;
    color: var(--navy-blue);
    text-transform: uppercase;
    letter-spacing: -0.2px;
  }
  .card--back .brand { left: 300px; width: 260px; top: 102px; }
  .card--back .brand__name { font-size: 20px; line-height: 1.1; }
  .card--back .brand__dot { width: 12px; height: 12px; }
  .card--back .brand__tagline { font-size: 14px; line-height: 1.2; }

  .contact {
    position: absolute;
    left: 0;
    right: 0;
    top: 181px;
    text-align: center;
    color: var(--ink);
  }
  .contact__lead { font-size: 16px; line-height: 24px; }
  .contact__phones { font-size: 22px; line-height: 26px; font-weight: 600; }
  .contact__or { font-size: 14px; font-weight: 400; }
  .contact__alt { font-size: 15px; line-height: 20px; }
  .contact__email {
    font-size: 20px;
    line-height: 28px;
    font-weight: 600;
    font-style: italic;
    color: var(--fresh-green);
  }
  .contact__help { font-size: 16px; line-height: 20px; }
</style>
</head>
<body>
  <section class="card card--front">
    <div class="water-photo" role="img" aria-label="Photograph of a clear blue water splash"></div>
    <div class="brand">
      <div class="brand__name"><span class="brand__dot"></span>CEDAR HOLLOW</div>
      <div class="brand__tagline">Purified Spring Water</div>
    </div>
    <div class="price">PRICE $100</div>
  </section>

  <section class="card card--back">
    <div class="water-photo" role="img" aria-label="Photograph of a blue water wave"></div>
    <p class="usage-note">This card is to be used<br>to access water refills<br>at any Cedar Hollow<br>water vending machines</p>
    <div class="brand">
      <div class="brand__name"><span class="brand__dot"></span>CEDAR HOLLOW</div>
      <div class="brand__tagline">Purified Spring Water</div>
    </div>
    <div class="contact">
      <p class="contact__lead">Please contact</p>
      <p class="contact__phones">(869) 418 2930 <span class="contact__or">or</span> (869) 534 1276</p>
      <p class="contact__alt">or</p>
      <p class="contact__email">clearflowbox@mailvista.example</p>
      <p class="contact__help">for any assistance or recharging of card</p>
    </div>
  </section>
</body>
</html>
```